Postcard for Construction Industry

www.brindlequants.com is our website.

We offer services to construction companies to read blueprints and give them a materials quantity list of how much work they need to do on a project. We service all types of companies such as painting, flooring, siding, drywall, Acoustical ceiling tile, framing, millwork, and much more.

I want a postcard designed that can be sent via email AND regular mail to introduce our company.

I've also attached another document with more detailed explanation, pricing, etc.

Important:
The postcard must appeal to the construction industry so they pick it up and read it.

Target Market(s)

Construction Industry

Industry/Entity Type

Construction

Font styles to use
Serif

Requirements
Must have
• Call to Action -
• Register on our site
• Get a FREE Quote
• Trades Serviced should be referenced on front so the person reading it immediately knows 2 things. Free Construction Takeoffs. List of Trades.
Nice to have
• Construction Images
• It's so EASY!!!
• -You load your plans
• -We give you a quote
• -If you approve, we do the work!
• NO OBLIGATION TO PURCHASE
Should not have
• Pricing - other than FREE Quotes
• Should not have phone number Prominent. It can be small on the back. (I want them to register via website)

```html
<!DOCTYPE html>
<html lang="en">
<head>
<meta charset="utf-8">
<title>Brindle Quants Postcard</title>
<link rel="stylesheet" href="https://fonts.googleapis.com/css2?family=League+Gothic&family=Roboto+Condensed:wght@400;700&family=Open+Sans:wght@400;700&display=swap">
<style>
:root{
  --blue:#0d58a5;
  --blue-text:#1668b8;
  --url-blue:#4ea6ea;
  --ink:#1c1c1c;
  --dark:#2a2a2c;
  --grey-line:#3a3a3c;
  --paper:#ffffff;
  --bg:#e3e3e3;
}
*{margin:0;padding:0;box-sizing:border-box}
html,body{width:1200px;height:1200px;overflow:hidden;background:var(--bg)}
.card{position:absolute;left:230px;width:740px;height:573px;background:var(--paper);overflow:hidden}
.card--front{top:16px}
.card--back{top:611px}
.abs{position:absolute}
.cond{font-family:"League Gothic",sans-serif;font-weight:400;text-transform:uppercase;white-space:nowrap}
.small{font-family:"Roboto Condensed",sans-serif}
.shapes{position:absolute;left:0;top:0}

/* front */
.brand{left:40px;top:52px;font-family:"League Gothic",sans-serif;font-size:54px;letter-spacing:2px;color:var(--blue);line-height:1;white-space:nowrap}
.brand-tag{left:42px;top:112px;font-family:"Open Sans",sans-serif;font-size:10px;color:var(--blue-text);letter-spacing:.3px}
.hero-title{left:28px;top:200px;color:#fff;line-height:1}
.hero-title .l1{font-size:34px;display:block}
.hero-title .l2{font-size:50px;display:block;margin-top:2px}
.no-obligation{left:31px;top:335px;font-size:44px;line-height:1;color:var(--ink)}
.register{border:3px solid var(--blue);border-top:none;background:var(--dark);border-radius:0 0 18px 18px;color:#fff;text-align:center;line-height:1.05}
.register .url{color:var(--url-blue);display:block}
.register--front{left:414px;top:308px;width:305px;height:94px;padding-top:18px;font-size:28px}
.section-head{font-family:"League Gothic",sans-serif;font-weight:400;color:var(--blue-text);font-size:36px;line-height:1;white-space:nowrap}
.easy{left:31px;top:402px}
.trades{left:248px;top:406px}
.list{list-style:none;font-family:"Roboto Condensed",sans-serif;font-size:14px;color:var(--ink);white-space:nowrap}
.list li{position:relative;padding-left:12px;line-height:23px}
.list li::before{content:"";position:absolute;left:0;top:8px;width:7px;height:7px;border-radius:50%;background:var(--blue-text)}
.easy-list{left:31px;top:441px}
.trade-list{top:446px;font-size:13.5px}
.trade-list li{line-height:19px}
.trade-list li::before{top:6px}
.divider{left:226px;top:408px;width:2px;height:92px;background:var(--blue-text)}
.badge{left:540px;top:416px;width:142px;height:142px;border-radius:50%;background:#fff;border:9px solid var(--dark);box-shadow:0 0 0 3px #fff,0 0 0 6px #c9c9c9;display:flex;flex-direction:column;align-items:center;justify-content:center;line-height:1}
.badge span{font-size:25px;color:var(--ink)}
.badge .mid{font-size:28px;color:var(--blue-text);margin:1px 0}
.badge .big{font-size:31px}

/* back */
.back-title{left:20px;top:28px;width:455px;text-align:center;font-size:32px;line-height:1;color:#fff}
.point{top:84px;height:76px;background:var(--dark);border:2px solid #fff;color:#fff;font-family:"Roboto Condensed",sans-serif;font-weight:700;font-size:13px;line-height:1.15;text-align:center;text-transform:uppercase;display:flex;align-items:center;justify-content:center;padding:12px 6px 0}
.tick{position:absolute;left:50%;top:-16px;width:30px;height:30px;margin-left:-15px}
.reasons-head{left:35px;top:195px;font-family:"Open Sans",sans-serif;font-weight:700;font-size:14px;color:var(--blue-text)}
.reasons{left:35px;top:212px;font-family:"Open Sans",sans-serif;font-size:13px}
.reasons li{line-height:18px}
.reasons li::before{top:6px}
.intro{left:34px;top:282px;width:368px;font-size:12.2px;line-height:18.2px;color:var(--ink)}
.volume{left:34px;top:387px;font-family:"Open Sans",sans-serif;font-weight:700;font-size:13.5px;color:var(--ink);line-height:18px}
.volume .fast{color:var(--blue-text);font-size:14.5px;display:block}
.register--back{left:31px;top:440px;width:247px;height:70px;border-top:3px solid var(--blue);border-radius:22px;padding-top:11px;font-size:22px}
.laptop{left:294px;top:410px;width:172px;height:101px}
.address{left:520px;top:44px;font-size:12px;line-height:18px;color:var(--ink)}
.stamp{left:646px;top:31px;width:63px;height:64px;background:#c8c9cc}
</style>
</head>
<body>

<section class="card card--front">
  <svg class="shapes" width="740" height="573" viewBox="0 0 740 573">
    <defs>
      <linearGradient id="plan" x1="0" y1="0" x2="1" y2="1">
        <stop offset="0" stop-color="#f6f7f9"/>
        <stop offset="1" stop-color="#d9dce1"/>
      </linearGradient>
      <linearGradient id="lower" x1="0" y1="0" x2="0" y2="1">
        <stop offset="0" stop-color="#ffffff"/>
        <stop offset="1" stop-color="#eeeff1"/>
      </linearGradient>
    </defs>
    <rect x="0" y="300" width="740" height="230" fill="url(#lower)"/>
    <rect x="0" y="157" width="345" height="7" fill="var(--grey-line)"/>
    <polygon points="0,168 368,168 327,307 0,307" fill="var(--blue)"/>
    <polygon points="373,0 740,0 740,300 327,300" fill="url(#plan)" role="img" aria-label="Architectural floor plan blueprints with rolled drawings"/>
    <polygon points="370,0 378,0 331,300 323,300" fill="var(--blue)"/>
    <polygon points="320,300 740,300 740,310 318,310" fill="#3f82c8"/>
    <rect x="0" y="528" width="740" height="7" fill="var(--grey-line)"/>
    <rect x="0" y="541" width="740" height="32" fill="var(--blue)"/>
  </svg>

  <div class="abs brand">BRINDLE QUANTS</div>
  <div class="abs brand-tag">COMMERCIAL CONSTRUCTION PROFESSIONALS</div>

  <h1 class="abs hero-title cond"><span class="l1">Commercial Construction</span><span class="l2">Takeoff Services</span></h1>

  <div class="abs no-obligation cond">No obligation to purchase</div>
  <div class="abs register register--front cond">Register to start a project on<span class="url">www.brindlequants.com</span></div>

  <h2 class="abs section-head easy">It's so EASY!!!</h2>
  <ul class="abs list easy-list">
    <li>You load your plans</li>
    <li>We give you a quote</li>
    <li>If you approve, we do the work!</li>
  </ul>

  <div class="abs divider"></div>
  <h2 class="abs section-head trades">Trades Serviced</h2>
  <ul class="abs list trade-list" style="left:251px">
    <li>Floor &amp; Wallcoverings</li>
    <li>Painting</li>
    <li>Roofing</li>
  </ul>
  <ul class="abs list trade-list" style="left:313px;top:465px">
    <li>Sheetrock</li>
    <li>Siding</li>
  </ul>
  <ul class="abs list trade-list" style="left:390px">
    <li>Millwork</li>
    <li>Foundations &amp; Paving</li>
    <li>And many more...</li>
  </ul>

  <div class="abs badge cond"><span>Free quote</span><span class="mid">On every</span><span class="big">Project</span></div>
</section>

<section class="card card--back">
  <svg class="shapes" width="740" height="573" viewBox="0 0 740 573">
    <defs>
      <linearGradient id="sheet" x1="0" y1="0" x2="0" y2="1">
        <stop offset="0" stop-color="#f2f3f5"/>
        <stop offset="1" stop-color="#ffffff"/>
      </linearGradient>
    </defs>
    <polygon points="0,175 441,175 370,528 0,528" fill="url(#sheet)"/>
    <polygon points="0,0 478,0 441,175 0,175" fill="var(--blue)"/>
    <polygon points="478,0 508,0 398,528 368,528" fill="#d4d6d9"/>
    <polygon points="492,0 508,0 398,528 382,528" fill="#55575a"/>
    <rect x="0" y="528" width="740" height="7" fill="var(--grey-line)"/>
    <rect x="0" y="538" width="740" height="35" fill="var(--blue)"/>
  </svg>

  <h2 class="abs back-title cond">Commercial Construction Takeoff Services</h2>

  <div class="abs point" style="left:26px;width:132px">
    <svg class="tick" viewBox="0 0 30 30"><circle cx="15" cy="15" r="14" fill="var(--dark)" stroke="#fff" stroke-width="2"/><path d="M8 15l5 5 9-10" fill="none" stroke="#fff" stroke-width="3"/></svg>
    Commercial construction takeoff services</div>
  <div class="abs point" style="left:174px;width:131px">
    <svg class="tick" viewBox="0 0 30 30"><circle cx="15" cy="15" r="14" fill="var(--dark)" stroke="#fff" stroke-width="2"/><path d="M8 15l5 5 9-10" fill="none" stroke="#fff" stroke-width="3"/></svg>
    Can't find the budget for a full-time expert?</div>
  <div class="abs point" style="left:318px;width:132px">
    <svg class="tick" viewBox="0 0 30 30"><circle cx="15" cy="15" r="14" fill="var(--dark)" stroke="#fff" stroke-width="2"/><path d="M8 15l5 5 9-10" fill="none" stroke="#fff" stroke-width="3"/></svg>
    Do you want to verify the quantities from your subs?</div>

  <div class="abs reasons-head">Reasons:</div>
  <ul class="abs list reasons">
    <li>Can't find the time to bid new projects?</li>
    <li>Can't find the budget for a full-time expert?</li>
    <li>Double check your quantities before signing a contract?</li>
  </ul>

  <p class="abs intro small">Thank you for your interest in Brindle Quants. We provide a service for our customers who don't have enough time to handle their full inbox of RFP's and Bid Requests. We will read the blueprints, specs, and notes for you and provide you with everything your estimator needs: quantities, area, notes, etc. We provide this service for most commercial construction trades!</p>

  <div class="abs volume">High-Volume Pricing Discounts Available<span class="fast">Expedited Delivery As Low as 24hrs</span></div>

  <div class="abs register register--back cond">Register to start a project on<span class="url">www.brindlequants.com</span></div>

  <svg class="abs laptop" viewBox="0 0 172 101" role="img" aria-label="Laptop showing a blueprint with a pen and measuring tape">
    <rect x="18" y="0" width="134" height="88" rx="3" fill="#111"/>
    <rect x="24" y="6" width="122" height="76" fill="#dfe3e8"/>
    <rect x="0" y="88" width="172" height="8" rx="3" fill="#b9bcc0"/>
  </svg>

  <div class="abs address small">Brindle Quants<br>PO Box 418<br>Marietta, GA 30061-0418</div>
  <div class="abs stamp"></div>
</section>

</body>
</html>
```